Business card por a urban DJ, up scale audience target

Need a sober design, modern, conservative colors but i can consider some options, y play rnb, hip hop, EDM and top40.

Business card for contact and personal info, double sided, use logo attrached please; im 42 so i need a card acording to my age an target audience.

Target Market(s)

Adult people, up scale audience

Industry/Entity Type

Music Download

Contact Information for Business Card

Cel (318) 4207265518 www.lumadrift.com

Requirements
Must have
• open mind
Nice to have
• open mind
Should not have
• DJ

```html
<!DOCTYPE html>
<html lang="en">
<head>
<meta charset="utf-8">
<title>Luma Drift – Business Card</title>
<link rel="stylesheet" href="https://fonts.googleapis.com/css2?family=Arimo:wght@400&family=Exo+2:wght@600;800&display=swap">
<style>
  :root {
    --backdrop: #808080;
    --ink: #2d2b2b;
    --paper: #ffffff;
    --rule-soft: #d9d9d9;
  }
  * { box-sizing: border-box; margin: 0; padding: 0; }
  html, body {
    width: 992px; height: 1200px; overflow: hidden;
    background: var(--backdrop);
  }
  .canvas { position: relative; width: 992px; height: 1200px; }

  .card { position: absolute; left: 68px; width: 868px; height: 496px; overflow: hidden; }

  /* Front */
  .card--front { top: 66px; background: var(--ink); }
  .brand-front {
    position: absolute; left: 0; right: 0; top: 150px;
    display: flex; align-items: center; justify-content: center; gap: 22px;
  }
  .brand-front__mark { width: 40px; height: 40px; background: var(--paper); }
  .brand-front__name {
    font-family: "Exo 2", sans-serif; font-weight: 800;
    font-size: 150px; line-height: 1; letter-spacing: 6px; color: var(--paper);
  }
  .front-web {
    position: absolute; left: 0; right: 0; top: 428px;
    display: flex; align-items: center; justify-content: center; gap: 26px;
  }
  .front-web__rule { width: 142px; height: 1px; background: var(--rule-soft); }
  .front-web__url {
    font-family: "Arimo", sans-serif; font-size: 23px; color: var(--paper);
  }

  /* Back */
  .card--back { top: 626px; background: var(--paper); }
  .back-band { position: absolute; left: 0; top: 0; width: 168px; height: 100%; background: var(--ink); }
  .brand-back {
    position: absolute; left: 186px; top: 60px;
    display: flex; align-items: center; gap: 14px;
  }
  .brand-back__mark { width: 26px; height: 26px; background: var(--ink); }
  .brand-back__name {
    font-family: "Exo 2", sans-serif; font-weight: 800;
    font-size: 100px; line-height: 1; letter-spacing: 4px; color: var(--ink);
  }
  .person__name {
    position: absolute; right: 38px; top: 232px;
    font-family: "Exo 2", sans-serif; font-weight: 600;
    font-size: 33px; color: var(--ink); letter-spacing: 0.5px;
  }
  .person__rule { position: absolute; left: 197px; top: 285px; width: 536px; height: 3px; background: var(--ink); }
  .person__role {
    position: absolute; right: 38px; top: 272px;
    font-family: "Arimo", sans-serif; font-size: 22px; color: var(--ink);
  }
  .contacts { position: absolute; left: 197px; top: 338px; list-style: none; }
  .contacts li {
    display: flex; align-items: center; gap: 16px; height: 34px;
    font-family: "Arimo", sans-serif; font-size: 21px; color: var(--ink);
  }
  .contacts svg { width: 22px; height: 22px; flex: none; }
</style>
</head>
<body>
<main class="canvas">

  <section class="card card--front" aria-label="Card front">
    <div class="brand-front">
      <span class="brand-front__mark"></span>
      <span class="brand-front__name">LUMA</span>
    </div>
    <div class="front-web">
      <span class="front-web__rule"></span>
      <span class="front-web__url">www.lumadrift.com</span>
      <span class="front-web__rule"></span>
    </div>
  </section>

  <section class="card card--back" aria-label="Card back">
    <div class="back-band"></div>
    <div class="brand-back">
      <span class="brand-back__name">LUMA</span>
      <span class="brand-back__mark"></span>
    </div>

    <h1 class="person__name">Rowan Hale</h1>
    <div class="person__rule"></div>
    <p class="person__role">Director</p>

    <ul class="contacts">
      <li>
        <svg viewBox="0 0 22 22" aria-hidden="true"><rect width="22" height="22" fill="#2d2b2b"/><path d="M7 4 L9.5 4 L10.5 8 L8.8 9.2 Q10 12.5 12.8 13.8 L14 12 L18 13 L18 15.5 Q17 18 14 17.5 Q6 15 4.5 7 Q4.5 4.5 7 4Z" fill="#fff"/></svg>
        <span>(318) 4207265518</span>
      </li>
      <li>
        <svg viewBox="0 0 22 22" aria-hidden="true"><rect width="22" height="22" fill="#2d2b2b"/><rect x="4" y="6" width="14" height="10" fill="#fff"/><path d="M4 6 L11 12 L18 6" fill="none" stroke="#2d2b2b" stroke-width="1.4"/></svg>
        <span>info@lumadrift.com</span>
      </li>
      <li>
        <svg viewBox="0 0 22 22" aria-hidden="true"><rect width="22" height="22" fill="#2d2b2b"/><circle cx="11" cy="11" r="7" fill="#fff"/><path d="M11 4 V18 M4 11 H18 M6 7 Q11 9 16 7 M6 15 Q11 13 16 15" fill="none" stroke="#2d2b2b" stroke-width="1.2"/></svg>
        <span>www.lumadrift.com</span>
      </li>
      <li>
        <svg viewBox="0 0 22 22" aria-hidden="true"><rect width="22" height="22" fill="#2d2b2b"/><path d="M11 18 Q5 11 5 9 A6 6 0 0 1 17 9 Q17 11 11 18Z" fill="#fff"/><circle cx="11" cy="9" r="2.2" fill="#2d2b2b"/></svg>
        <span>PO Box 4417 Kent Town SA 5071</span>
      </li>
    </ul>
  </section>

</main>
</body>
</html>
```